Company Business Card (Company Promotions)

We want a Business Card that is both Elegant & High Class. We want the card stock thick and unique. We want it to build our Brand Name. We service Automobile dealerships & owners who drive luxury & exotic automobiles that cost an average of $75K. We provide towing services for Luxury & Exotic vehicles. Our colors are Black & Construction Yellow (Gold).
We are manufacture certified for Valdora Kent, RQT, PUKA, ELVO, Tavrine, HJ, Colvesi, Pendrel, Casteduvro, Ombra & Sorvanel. We have authorization to use their logo's.
Enclosed is our old business card. We only used the unusual & Unique brands on the cards but are open to the use of all of them. We also use the Federal Competence Badge that identifies our abilities.

Also enclosed is the name font that we use.

Target Market(s)

Business, Executive, Hi end people that drive finer luxury &/or exotic automobiles.

Industry/Entity Type

Business

Contact Information for Business Card

We market our name. Haul Crestmark. Business address is: 4812 Willowmere Lane, NE Ste: 210, Atlanta, GA 30399 Phone: 404-555-0148. Web address is crestmarkhaul-example.com
Manufacture Certified / Nationally Certified

Font styles to use
Other font styles liked:
• AR DESTINE (in Italic's)

Colors
ffc214

Requirements
Must have
• Must have the at least 5 of the manufacture logo's and the Guild Council Emblem (see on other business card)
Nice to have
• Place the manfacture logo's on the back.
Should not have
• No other colors than Black, Yellow & White

```html
<!DOCTYPE html>
<html lang="en">
<head>
<meta charset="utf-8">
<title>Haul Crestmark – Business Card</title>
<link href="https://fonts.googleapis.com/css2?family=Russo+One&family=Open+Sans:wght@400;600&display=swap" rel="stylesheet">
<style>
  :root {
    --black: #0a0a0a;
    --yellow: #ffc214;
    --white: #ffffff;
    --backdrop: #e9e6df;
  }
  * { box-sizing: border-box; margin: 0; padding: 0; }
  html, body { width: 1200px; height: 902px; overflow: hidden; }
  body { background: var(--backdrop); position: relative; font-family: "Open Sans", sans-serif; }

  .card { position: absolute; width: 560px; height: 320px; background: var(--black); overflow: hidden; }

  /* Front */
  .card-front { left: 80px; top: 80px; border: 10px solid var(--yellow); }
  .card-front .badge { position: absolute; left: 30px; top: 92px; width: 116px; height: 128px; }
  .card-front .brand { position: absolute; left: 160px; top: 100px; width: 360px; }

  .brand-name {
    font-family: "Russo One", sans-serif;
    color: var(--yellow);
    font-size: 38px;
    letter-spacing: 1px;
    line-height: 1;
    text-transform: uppercase;
    white-space: nowrap;
  }
  .brand-rule { height: 3px; background: var(--yellow); margin: 6px 0 5px; }
  .brand-tagline { color: var(--yellow); font-size: 16px; white-space: nowrap; }

  /* Back */
  .card-back { left: 560px; top: 500px; }
  .card-back .bands { position: absolute; inset: 0; }
  .card-back .badge { position: absolute; left: 22px; top: 92px; width: 80px; height: 90px; }
  .card-back .brand { position: absolute; left: 112px; top: 104px; width: 240px; }
  .card-back .brand-name { font-size: 24px; letter-spacing: 0.5px; }
  .card-back .brand-rule { height: 2px; margin: 4px 0 3px; }
  .card-back .brand-tagline { font-size: 11px; }

  .maker { position: absolute; font-family: "Open Sans", sans-serif; font-weight: 600; font-size: 12px; color: var(--black); white-space: nowrap; }

  .contact { position: absolute; right: 20px; top: 168px; text-align: right; color: var(--white); font-size: 13px; line-height: 21px; }
  .contact-line { display: flex; justify-content: flex-end; align-items: center; gap: 8px; white-space: nowrap; }
  .contact-icon { width: 14px; height: 14px; background: var(--yellow); display: inline-flex; align-items: center; justify-content: center; }
  .contact-spacer { width: 14px; display: inline-block; }
</style>
</head>
<body>

  <section class="card card-front" aria-label="Business card front">
    <svg class="badge" viewBox="0 0 116 128" role="img" aria-label="Federal Competence Badge">
      <path d="M8 14 Q58 -6 108 14 L104 78 Q96 108 58 124 Q20 108 12 78 Z" fill="var(--white)" stroke="var(--yellow)" stroke-width="4"/>
    </svg>
    <div class="brand">
      <div class="brand-name">Haul Crestmark</div>
      <div class="brand-rule"></div>
      <div class="brand-tagline">Manufacture Certified / Nationally Certified</div>
    </div>
  </section>

  <section class="card card-back" aria-label="Business card back">
    <svg class="bands" viewBox="0 0 560 320" preserveAspectRatio="none" aria-hidden="true">
      <polygon points="220,0 560,0 560,140" fill="var(--yellow)"/>
      <polygon points="0,180 0,320 360,320" fill="var(--yellow)"/>
    </svg>

    <span class="maker" style="left:300px;top:14px">RQT</span>
    <span class="maker" style="left:356px;top:14px">Valdora Kent</span>
    <span class="maker" style="left:470px;top:14px">Pendrel</span>
    <span class="maker" style="left:486px;top:48px">ELVO</span>

    <span class="maker" style="left:18px;top:236px">Tavrine</span>
    <span class="maker" style="left:86px;top:244px">Ravelle Moto</span>
    <span class="maker" style="left:18px;top:286px">Terrow</span>
    <span class="maker" style="left:88px;top:286px">Vantrelli</span>
    <span class="maker" style="left:180px;top:292px">Fennick</span>

    <svg class="badge" viewBox="0 0 116 128" role="img" aria-label="Federal Competence Badge">
      <path d="M8 14 Q58 -6 108 14 L104 78 Q96 108 58 124 Q20 108 12 78 Z" fill="var(--white)" stroke="var(--yellow)" stroke-width="4"/>
    </svg>
    <div class="brand">
      <div class="brand-name">Haul Crestmark</div>
      <div class="brand-rule"></div>
      <div class="brand-tagline">Manufacture Certified / Nationally Certified</div>
    </div>

    <div class="contact">
      <div class="contact-line">404-555-0148
        <span class="contact-icon"><svg width="10" height="10" viewBox="0 0 10 10"><path d="M2 1 L4 1 L4.5 3 L3.5 4 Q4.5 6 6 6.5 L7 5.5 L9 6 L9 8 Q8 9 7 9 Q2 8 1 3 Q1 2 2 1Z" fill="var(--black)"/></svg></span>
      </div>
      <div class="contact-line">crestmarkhaul-example.com
        <span class="contact-icon"><svg width="10" height="10" viewBox="0 0 10 10"><circle cx="5" cy="5" r="4" fill="none" stroke="var(--black)" stroke-width="1.2"/><path d="M1 5 H9 M5 1 V9" stroke="var(--black)" stroke-width="1"/></svg></span>
      </div>
      <div class="contact-line">4812 Willowmere Lane, NE Ste: 210
        <span class="contact-icon"><svg width="10" height="10" viewBox="0 0 10 10"><path d="M5 9.5 Q1.5 5.5 1.5 3.8 A3.5 3.5 0 0 1 8.5 3.8 Q8.5 5.5 5 9.5Z" fill="var(--black)"/><circle cx="5" cy="3.8" r="1.2" fill="var(--yellow)"/></svg></span>
      </div>
      <div class="contact-line">Atlanta, GA 30399 <span class="contact-spacer"></span></div>
    </div>
  </section>

</body>
</html>
```